stationary
envelopes, letterhead, biz card
I need single sided standard sized Business Card [3.5" x 2"]
doesnt matter whatever looks good
Professional
Morris Delvane
President
4612 Wintermoor Rd Ste 208-517
morris@vandrex.com
www.vandrex.com

```html
<!DOCTYPE html>
<html lang="en">
<head>
<meta charset="utf-8">
<title>Vandrex Business Card</title>
<link href="https://fonts.googleapis.com/css2?family=Questrial&display=swap" rel="stylesheet">
<style>
  :root {
    --backdrop: #2a2a2c;
    --card: #f4f4f4;
    --card-shade: #e4e4e4;
    --ink: #2b2b2e;
    --ink-soft: #4a4a4e;
    --accent: #2aa3dc;
    --rule: #6b6b6f;
  }
  * { margin: 0; padding: 0; box-sizing: border-box; }
  html, body {
    width: 1200px;
    height: 901px;
    overflow: hidden;
    background: var(--backdrop);
    font-family: "Questrial", sans-serif;
  }
  .stage {
    width: 1200px;
    height: 901px;
    display: flex;
    align-items: center;
    justify-content: center;
  }
  .business-card {
    position: relative;
    width: 1050px;
    height: 600px;
    background: linear-gradient(135deg, #fbfbfb 0%, var(--card) 55%, var(--card-shade) 100%);
    border-radius: 22px;
    overflow: hidden;
    display: flex;
    box-shadow: 0 20px 50px rgba(0,0,0,0.45);
  }
  .business-card::after {
    content: "";
    position: absolute;
    left: 0; right: 0; bottom: 0;
    height: 12px;
    background: var(--accent);
  }
  .brand-side {
    width: 590px;
    display: flex;
    align-items: center;
    justify-content: center;
    gap: 24px;
  }
  .brand-mark {
    width: 46px;
    height: 46px;
    background: var(--accent);
  }
  .brand-name {
    font-size: 84px;
    letter-spacing: 4px;
    color: var(--ink);
    line-height: 1;
  }
  .divider {
    width: 2px;
    background: var(--rule);
    margin: 120px 0 130px;
  }
  .contact-side {
    flex: 1;
    padding: 120px 0 0 40px;
    color: var(--ink-soft);
    font-size: 26px;
    line-height: 1.32;
  }
  .contact-name {
    font-size: 34px;
    color: var(--ink);
  }
  .contact-title {
    margin-bottom: 30px;
  }
  .contact-web {
    margin-top: 36px;
    color: var(--ink);
  }
</style>
</head>
<body>
  <main class="stage">
    <article class="business-card">
      <section class="brand-side">
        <span class="brand-mark"></span>
        <span class="brand-name">VANDREX</span>
      </section>
      <div class="divider"></div>
      <section class="contact-side">
        <p class="contact-name">Morris Delvane</p>
        <p class="contact-title">President</p>
        <p class="contact-address">4612 Wintermoor<br>Rd Ste 208-517</p>
        <p class="contact-phone">P: 555.410.2786</p>
        <p class="contact-fax">F: 555.730.4419</p>
        <p class="contact-email">E: morris@vandrex.com</p>
        <p class="contact-web">www.vandrex.com</p>
      </section>
    </article>
  </main>
</body>
</html>
```